Local Chiropractor Needs Up Scale Webdesign

This website needs to have an upscale look with a very modern feel. Below is the information and websites to reference

Add Logo that is attached

Build a color scheme similar to this website image titled "chiro-1"

Must Include these pages in a horizontal menu bar in this order:
Home, Meet Our Staff, Patient Testimonials, Videos, Work Place Wellness, Contact

Build a "classy looking" Make An Appointment Button into the header with the contact info below

Phone Number:
555-314-2719

Address:
3168 Pelham Orchard Lane, #240
Maplewater, MN 55390

This website needs 4 rotating banners. Please reference a layout similar to this for the banners: http://drmorlatz.example/. However design it nicer than this website, this website is very boring and doesn't flow with the colors properly

Below are the description for each banner

Rotating Banner #1
Use Image: Pediatrics
Two lines of text. First line title line, second description. Use Latin text for fill

Rotating Banner #2
Use Image: Aging Gracefully

Rotating Banner #3
Use Image: Pregnancy

Rotating Banner #4
Use Image: Athletics

I'd like to see a free consultation box similar to the "chiro-1" image. Fields to include are: First Name, Last Name, Phone Number, Comments.

For the body, please fill it with latin text. Please design a professional body layout. You can include a box in the right column for the hours

Office Hours
Monday: 8:00-11:00, 2:00-5:00
Tuesday: 8:30-11:00, 2:00-5:30
Wednesday: 8:00-11:00, 2:00-5:00
Thursday: 10:00-12:00, 2:30-5:00
Friday: 8:00-10:00, 1:00-5:00
Saturday: Closed
Sunday: Closed

For the footer please design something similar to the: http://drmorlatz.example/

Also include in the Footer: Powered by Brightline Site Works

```html
<!DOCTYPE html>
<html lang="en">
<head>
<meta charset="utf-8">
<title>Brookhaven Spine &amp; Wellness</title>
<link href="https://fonts.googleapis.com/css2?family=Lato:ital,wght@0,400;0,700;0,900;1,700;1,900&display=swap" rel="stylesheet">
<style>
:root{
  --dark:#2b2b2b;
  --dark-2:#3a3a3a;
  --dark-3:#333333;
  --green:#7fb414;
  --green-light:#8dc21f;
  --text:#555555;
  --muted:#8a8a8a;
  --line:#e2e2e2;
  --white:#ffffff;
}
*{box-sizing:border-box;margin:0;padding:0}
html,body{width:692px;height:1200px;overflow:hidden}
body{position:relative;font-family:"Lato",sans-serif;color:var(--text);background:var(--white);font-size:6.5px;line-height:1.6}
.abs{position:absolute}
a{color:inherit;text-decoration:none}

/* header */
.site-header{left:0;top:0;width:692px;height:64px;background:var(--dark)}
.brand{display:flex;align-items:center;gap:5px}
.brand-mark{width:11px;height:11px;border-radius:50%;background:var(--green)}
.brand-name{font-weight:700;color:var(--white);font-size:10px;line-height:1.15}
.site-header .brand{left:93px;top:15px}
.contact-item{display:flex;align-items:center;gap:8px;color:var(--white);font-size:6px;line-height:1.4}
.contact-item svg{width:12px;height:12px;fill:#6a6a6a}
.contact-item small{display:block;color:#8c8c8c;font-size:5.5px}
.contact-phone{left:317px;top:16px}
.contact-address{left:402px;top:16px}
.btn-appointment{left:513px;top:13px;width:86px;height:22px;background:linear-gradient(var(--green-light),var(--green));color:var(--white);font-weight:900;font-size:5.8px;display:flex;align-items:center;justify-content:center;border-radius:2px}

/* nav */
.main-nav{left:93px;top:49px;width:506px;height:32px;background:linear-gradient(#ffffff,#ececec);border:1px solid #d4d4d4;z-index:3;display:flex;justify-content:center;align-items:center}
.main-nav a{position:relative;font-size:5.8px;color:#555;padding:0 6px;border-left:1px solid #d8d8d8;line-height:9px}
.main-nav a:first-child{border-left:0}
.main-nav a::before{content:"";position:absolute;left:50%;top:-11px;margin-left:-1.5px;border:1.5px solid transparent;border-top:2px solid #999}
.main-nav a.active{color:var(--dark)}
.main-nav a.active::after{content:"";position:absolute;left:0;right:0;bottom:-11px;height:2px;background:var(--green)}

/* hero */
.hero{left:0;top:64px;width:692px;height:239px;background:linear-gradient(100deg,#4f6b25 0%,#7e9a3a 30%,#a9b97a 48%,#5d7a2a 70%,#2f4a16 100%)}
.hero-caption{left:94px;top:137px;width:212px;height:112px;background:rgba(20,20,20,.62);padding:4px}
.hero-caption-inner{border:1px solid rgba(255,255,255,.55);height:100%;padding:8px 9px}
.hero-caption h1{font-size:17px;font-weight:700;color:var(--white);line-height:1.2}
.hero-caption .rule{width:22px;height:2px;background:var(--green);margin:6px 0 7px}
.hero-caption p{color:var(--white);font-size:6.3px;font-weight:400;line-height:1.7}
.hero-arrows{display:flex;gap:4px;margin-top:11px}
.hero-arrows span{width:22px;height:20px;background:var(--green);display:flex;align-items:center;justify-content:center}
.hero-arrows svg{width:6px;height:6px;stroke:var(--white);stroke-width:2;fill:none}

/* callout band */
.callout{left:0;top:303px;width:692px;height:43px;background:var(--dark-3)}
.callout p{position:absolute;left:93px;top:16px;color:var(--white);font-weight:900;font-style:italic;font-size:7.2px}
.btn-outline{position:absolute;left:533px;top:12px;width:66px;height:19px;border:1px solid var(--white);color:var(--white);font-size:5.8px;font-weight:700;display:flex;align-items:center;justify-content:center;gap:3px;border-radius:2px}

/* intro */
.intro{left:93px;top:379px;width:332px}
.section-title{font-size:8.5px;color:var(--dark);font-weight:400;line-height:1.2}
.section-sub{font-size:4.5px;color:var(--muted)}
.title-rule{position:relative;height:1px;background:var(--line);margin:5px 0 9px}
.title-rule::before{content:"";position:absolute;left:0;top:0;width:21px;height:2px;background:var(--green)}
.intro p{font-size:5.9px;line-height:1.75;color:#707070;margin-bottom:10px}
.checklist{list-style:none;margin-top:14px}
.checklist li{display:flex;align-items:center;gap:5px;font-size:5.6px;font-weight:900;color:var(--dark);height:16px}
.checklist svg{width:6px;height:6px;stroke:var(--green);stroke-width:2;fill:none}

/* feature cards */
.card{top:607px;width:160px}
.card-media{height:94px}
.card h3{margin-top:10px;font-size:7.2px;font-weight:400;color:var(--dark)}
.card.highlight h3{color:var(--green)}
.card .section-sub{margin-top:1px}
.card .short-rule{width:21px;height:2px;background:var(--green);margin:6px 0 8px}
.card p{font-size:5.9px;line-height:1.85;color:#707070}
.read-more{display:flex;align-items:center;gap:3px;margin-top:5px;font-size:5.8px;font-weight:700;color:var(--dark)}
.card.highlight .read-more{color:var(--green)}

/* sidebar */
.hours{left:439px;top:380px;width:160px;height:131px;border:1px solid #d6d6d6}
.panel-head{background:var(--dark);color:var(--white);font-weight:900;font-size:7px;text-align:center;height:26px;line-height:26px}
.hours ul{list-style:none;padding:4px 7px 0}
.hours li{display:flex;justify-content:space-between;font-size:5.2px;color:#555;height:13px;line-height:13px}
.hours li.closed{color:var(--green)}

.consult{left:439px;top:520px;width:160px;height:265px;border:1px solid #d6d6d6}
.consult-head{position:relative;height:59px;text-align:center;color:var(--white)}
.consult-head svg{position:absolute;left:0;top:0;width:158px;height:59px}
.consult-head .lines{position:relative;padding-top:6px}
.consult-head .kicker{color:var(--green-light);font-size:5.8px;line-height:12px}
.consult-head .big{font-weight:900;font-size:9px;line-height:13px}
.consult-head .today{color:var(--green-light);font-size:5.5px;line-height:13px}
.consult form{padding:7px 8px}
.consult h4{font-size:7px;font-weight:400;color:var(--dark);margin-bottom:8px}
.consult label{display:block;font-size:5.4px;color:var(--dark);margin-bottom:2px}
.field{height:13px;border:1px solid #dcdcdc;margin-bottom:11px}
.field.focus{border-color:var(--green)}
.field.area{height:43px}
.btn-submit{display:inline-flex;align-items:center;gap:3px;width:55px;height:17px;justify-content:center;background:linear-gradient(var(--green-light),var(--green));color:var(--white);font-size:5.8px;font-weight:900;border-radius:2px;margin-top:-2px}

/* newsletter */
.newsletter{left:93px;top:821px;width:506px;height:128px;padding:7px;background:repeating-linear-gradient(45deg,#e4e4e4 0 2px,#ffffff 2px 5px)}
.newsletter-inner{background:var(--white);height:100%;text-align:center;padding-top:29px}
.newsletter h2{font-size:12.5px;font-weight:400;color:var(--dark);line-height:1.2}
.newsletter p{font-size:6px;color:#666;margin-top:3px}
.newsletter-form{display:flex;justify-content:center;gap:0;margin-top:16px}
.nl-input{width:129px;height:20px;border:1px solid #e0e0e0;display:flex;align-items:center;gap:8px;padding-left:8px;font-size:5.5px;font-style:italic;color:#888}
.nl-input svg{width:6px;height:6px;stroke:#777;fill:none;stroke-width:1}
.btn-subscribe{width:54px;height:20px;margin-left:5px;background:linear-gradient(var(--green-light),var(--green));color:var(--white);font-weight:900;font-size:5.8px;display:flex;align-items:center;justify-content:center;border-radius:2px}

/* footer */
.footer-top{left:0;top:984px;width:692px;height:36px;background:var(--dark-2)}
.footer-top .brand{position:absolute;left:93px;top:12px}
.footer-top .brand-name{font-size:9px}
.footer-top .brand-mark{width:9px;height:9px}
.socials{position:absolute;left:478px;top:9px;display:flex;gap:5px}
.socials span{width:16px;height:16px;border:1px solid #5a5a5a;background:#2a2a2a}
.socials span.on{background:var(--green);border-color:var(--green)}

.footer-main{left:0;top:1020px;width:692px;height:146px;background:var(--dark)}
.footer-col{position:absolute;top:27px;text-align:center}
.footer-col h5{font-size:6.5px;font-weight:700;color:#cfcfcf;letter-spacing:.2px}
.col-about{left:93px;width:158px}
.col-about p{text-align:left;margin-top:15px;font-size:5.8px;line-height:1.75;color:#7d7d7d}
.footer-links{display:flex;margin-top:9px;font-size:5.6px;color:#cfcfcf}
.footer-links a{padding:0 8px;border-left:1px solid #555}
.footer-links a:first-child{padding-left:0;border-left:0}
.footer-links a.accent{color:var(--green)}
.col-map{left:268px;width:157px}
.map{margin-top:15px;height:65px;border:2px solid #d8d8d8;background:linear-gradient(135deg,#e9e9e9,#d5d5d5 60%,#e2e2e2)}
.col-contact{left:440px;width:160px}
.col-contact .addr{margin-top:14px;font-size:6px;font-weight:700;color:#dcdcdc}
.col-contact ul{list-style:none;text-align:left;margin:5px 0 0 38px}
.col-contact li{display:flex;align-items:center;gap:8px;height:13px;font-size:5.6px;color:#9a9a9a}
.col-contact li svg{width:6px;height:6px;fill:#9a9a9a}
.col-contact li.accent{color:var(--green)}

.footer-bottom{left:0;top:1166px;width:692px;height:34px;background:var(--green-light)}
.footer-bottom .copy{position:absolute;left:93px;top:12px;font-size:5.6px;font-weight:700;color:var(--white)}
.footer-nav{position:absolute;left:285px;top:12px;display:flex;font-size:5.6px;color:var(--white);font-weight:700}
.footer-nav a{padding:0 6px;border-left:1px solid rgba(255,255,255,.6);line-height:8px}
.footer-nav a:first-child{border-left:0;padding-left:0}
.to-top{position:absolute;left:573px;top:9px;width:26px;height:17px;border:1px solid var(--white);display:flex;align-items:center;justify-content:center}
.to-top svg{width:6px;height:4px;stroke:var(--white);fill:none;stroke-width:1.4}
</style>
</head>
<body>

<header class="site-header abs">
  <div class="brand abs"><span class="brand-mark"></span><span class="brand-name">Brookhaven Spine<br>&amp; Wellness</span></div>
  <div class="contact-item contact-phone abs">
    <svg viewBox="0 0 24 24"><path d="M6.6 10.8a15.1 15.1 0 006.6 6.6l2.2-2.2c.3-.3.7-.4 1-.2 1.1.4 2.3.6 3.6.6.6 0 1 .4 1 1V20c0 .6-.4 1-1 1A17 17 0 013 4c0-.6.4-1 1-1h3.5c.6 0 1 .4 1 1 0 1.3.2 2.5.6 3.6.1.3 0 .7-.2 1z"/></svg>
    <div>555-314-2719<small>info@example.com</small></div>
  </div>
  <div class="contact-item contact-address abs">
    <svg viewBox="0 0 24 24"><path d="M12 3l10 9h-3v8h-5v-6h-4v6H5v-8H2z"/></svg>
    <div>Maplewater, MN 55390<small>3168 Pelham Orchard Lane, #240</small></div>
  </div>
  <a class="btn-appointment abs" href="#">MAKE AN APPOINTMENT</a>
</header>

<nav class="main-nav abs">
  <a href="#">HOME</a>
  <a href="#" class="active">MEET OUR STAFF</a>
  <a href="#">PATIENT TESTIMONIALS</a>
  <a href="#">VIDEOS</a>
  <a href="#">WORK PLACE WELLNESS</a>
  <a href="#">CONTACT</a>
</nav>

<section class="hero abs" role="img" aria-label="Banner photo: two older women jogging together along a sunlit forest path"></section>
<div class="hero-caption abs">
  <div class="hero-caption-inner">
    <h1>Your Title Goes Here</h1>
    <div class="rule"></div>
    <p>Lorem ipsum dolor sit amet, consectetur adipisicing elit, sed do eiusmod tempor incididunt ut labore et dolore magna aliqua.</p>
    <div class="hero-arrows">
      <span><svg viewBox="0 0 6 6"><path d="M4 0.5L1.5 3 4 5.5"/></svg></span>
      <span><svg viewBox="0 0 6 6"><path d="M2 0.5L4.5 3 2 5.5"/></svg></span>
    </div>
  </div>
</div>

<section class="callout abs">
  <p>DONEC SUSCIPIT VEHICULA TURPIS SED LUTPAT QUISQUE VITAE QUAM NEQUE?</p>
  <a class="btn-outline" href="#">Contact Us
    <svg width="6" height="5" viewBox="0 0 12 9" fill="none" stroke="#fff"><rect x=".5" y=".5" width="11" height="8"/><path d="M.5 .5L6 5l5.5-4.5"/></svg></a>
</section>

<main>
  <section class="intro abs">
    <h2 class="section-title">Hello Dear Visitor</h2>
    <div class="section-sub">This is an About Us Text</div>
    <div class="title-rule"></div>
    <p>Pellentesque habitant morbi tristique senectus et netus et malesuada fames ac turpis egestas. Donec faucibus aliquet dui, nec congue orci sagittis eget. Sed sit amet augue id nisi fringilla elementum ut nec augue. Fusce ultrices convallis enim eu interdum. Nam libero neque, congue id nisl vel, sagittis malesuada ex. Ut vel arcu sed ligula condimentum con sequat sed vehicula purus. Donec eu erat pharetra, euismod justo id, volutpat orci. Etiam ac tortor ut urna egestas cursus vel nec nisi. Vivamus molestie nec magna sit amet rutrum.</p>
    <p>Nullam maximus tincidunt metus, quis tempus libero vulputate non. Ut vitae aliquam urna, pharetra elementum ipsum. Phasellus maximus dolor orci. Pellentesque leo tortor, hendrerit sit amet rutrum. Imperdiet vel ligula. Cum sociis natoque penatibus et magnis dis parturient montes, nascetur ridiculus mus.</p>
    <ul class="checklist">
      <li><svg viewBox="0 0 6 6"><path d="M.5 3l1.8 1.8L5.5 1"/></svg>SED NON MASSA SIT AMET ENIM FEUGIAT BIBENDUM A ET ARCU</li>
      <li><svg viewBox="0 0 6 6"><path d="M.5 3l1.8 1.8L5.5 1"/></svg>CRAS ACCUMSAN TRISTIQUE EUISMOD. IN AC DIAM ET NULLA HENDRERIT</li>
      <li><svg viewBox="0 0 6 6"><path d="M.5 3l1.8 1.8L5.5 1"/></svg>FUSCE EU TELLUS PHARETRA, ULTRICES DUI VITAE RHONCUS</li>
      <li><svg viewBox="0 0 6 6"><path d="M.5 3l1.8 1.8L5.5 1"/></svg>NIBH. QUISQUE ID QUAM VELIT. MORBI MALESUADA LOREM A NISL MOLLIS TEMPUS</li>
    </ul>
  </section>

  <article class="card abs" style="left:93px">
    <div class="card-media" role="img" aria-label="Photo: two skiers descending a snowy slope" style="background:linear-gradient(160deg,#f1f3f5,#d6dbe0 55%,#eef0f2)"></div>
    <h3>Title Goes Here</h3>
    <div class="section-sub">This is Subtitle</div>
    <div class="short-rule"></div>
    <p>Placerat dapibus. Etiam ultrices nulla sed leo malesuada commodo bibendum orci vi verra. Sed rutrum dapibus feugiat. Iasellus et congue arcu.</p>
    <a class="read-more" href="#">Read More <svg width="6" height="5" viewBox="0 0 6 5" fill="none" stroke="currentColor" stroke-width=".8"><path d="M.5 2.5h4M3 1l1.5 1.5L3 4"/></svg></a>
  </article>

  <article class="card highlight abs" style="left:266px">
    <div class="card-media" role="img" aria-label="Photo with green tint: a small child playing with a parent" style="background:linear-gradient(135deg,#a9cf45,#93c02a 50%,#b7d966)"></div>
    <h3>Title Goes Here</h3>
    <div class="section-sub">This is Subtitle</div>
    <div class="short-rule"></div>
    <p>Placerat dapibus. Etiam ultrices nulla sed leo malesuada commodo bibendum orci vi verra. Sed rutrum dapibus feugiat. Iasellus et congue arcu.</p>
    <a class="read-more" href="#">Read More <svg width="6" height="5" viewBox="0 0 6 5" fill="none" stroke="currentColor" stroke-width=".8"><path d="M.5 2.5h4M3 1l1.5 1.5L3 4"/></svg></a>
  </article>

  <aside>
    <section class="hours abs">
      <div class="panel-head">OPENING HOURS</div>
      <ul>
        <li><span>Monday</span><span>8:00-11:00, 14:00-17:00</span></li>
        <li><span>Tuesday</span><span>8:30-11:00, 14:00-17:30</span></li>
        <li><span>Wednesday</span><span>8:00-11:00, 14:00-17:00</span></li>
        <li><span>Thursday</span><span>10:00-12:00, 14:30-17:00</span></li>
        <li><span>Friday</span><span>8:00-10:00, 13:00-17:00</span></li>
        <li class="closed"><span>Saturday</span><span>Closed</span></li>
        <li class="closed"><span>Sunday</span><span>Closed</span></li>
      </ul>
    </section>

    <section class="consult abs">
      <div class="consult-head">
        <svg viewBox="0 0 158 59" preserveAspectRatio="none"><path d="M0 0H158V48L79 59 0 48Z" fill="#2b2b2b"/></svg>
        <div class="lines">
          <div class="kicker">CONTACT US NOW &amp; GET YOUR</div>
          <div class="big">FREE CONSULTATION</div>
          <div class="today">TODAY !</div>
        </div>
      </div>
      <form>
        <h4>WELLNESS BEGINS HERE</h4>
        <label>First Name</label><div class="field"></div>
        <label>Last Name</label><div class="field focus"></div>
        <label>Phone Number</label><div class="field"></div>
        <label>Comments</label><div class="field area"></div>
        <span class="btn-submit">Submit <svg width="6" height="5" viewBox="0 0 6 5" fill="none" stroke="#fff" stroke-width=".8"><path d="M.5 2.5h4M3 1l1.5 1.5L3 4"/></svg></span>
      </form>
    </section>
  </aside>

  <section class="newsletter abs">
    <div class="newsletter-inner">
      <h2>NEWSLETTER SUBSCRIPTION</h2>
      <p>Subscribe and be the first one who is getting the latest news &amp; notes! We promise to keep your mails safe, NO SPAMS!</p>
      <div class="newsletter-form">
        <span class="nl-input"><svg viewBox="0 0 6 6"><path d="M1 5l.3-1.3L4.3.7l1 1-3 3z"/></svg>Enter Your Full Name</span>
        <span class="nl-input"><svg viewBox="0 0 6 6"><rect x=".5" y="1" width="5" height="4"/><path d="M.5 1L3 3.2 5.5 1"/></svg>Enter Your Email Address</span>
        <span class="btn-subscribe">Subscribe</span>
      </div>
    </div>
  </section>
</main>

<footer>
  <div class="footer-top abs">
    <div class="brand"><span class="brand-mark"></span><span class="brand-name">Brookhaven Spine &amp; Wellness</span></div>
    <div class="socials" aria-label="Social links">
      <span></span><span class="on"></span><span></span><span></span><span></span><span></span>
    </div>
  </div>

  <div class="footer-main abs">
    <div class="footer-col col-about">
      <h5>- ABOUT US -</h5>
      <p>Phasellus rhoncus sapien ipsum, at sollicitudin nunc rhoncus quis. Mauris gravida neque elementum est imperdiet, non vehicula risus finibus. Vivamus faucibus aliquet leo vitae laoreet. Cras commodo velit metus.</p>
      <div class="footer-links"><a href="#">Privacy Policy</a><a href="#" class="accent">Terms and Conditions</a><a href="#">FAQ</a></div>
    </div>
    <div class="footer-col col-map">
      <h5>- WE ARE HERE -</h5>
      <div class="map" role="img" aria-label="Map showing the clinic location"></div>
    </div>
    <div class="footer-col col-contact">
      <h5>- GET IN TOUCH -</h5>
      <div class="addr">3168 Pelham Orchard Lane, #240 Maplewater, MN 55390</div>
      <ul>
        <li><svg viewBox="0 0 24 24"><path d="M6.6 10.8a15.1 15.1 0 006.6 6.6l2.2-2.2c.3-.3.7-.4 1-.2 1.1.4 2.3.6 3.6.6.6 0 1 .4 1 1V20c0 .6-.4 1-1 1A17 17 0 013 4c0-.6.4-1 1-1h3.5c.6 0 1 .4 1 1 0 1.3.2 2.5.6 3.6.1.3 0 .7-.2 1z"/></svg>+1 555-314-2719</li>
        <li><svg viewBox="0 0 24 24"><path d="M6 2h12v6H6zM3 9h18v9h-3v4H6v-4H3zm5 6v5h8v-5z"/></svg>+1 555-314-2719</li>
        <li class="accent"><svg viewBox="0 0 24 24"><path d="M2 5h20v14H2zm2 2v.5l8 5.5 8-5.5V7z"/></svg>info@example.com</li>
        <li><svg viewBox="0 0 24 24"><path d="M12 2a7 7 0 017 7c0 5-7 13-7 13S5 14 5 9a7 7 0 017-7zm0 4a3 3 0 100 6 3 3 0 000-6z"/></svg>see in large map</li>
      </ul>
    </div>
  </div>

  <div class="footer-bottom abs">
    <div class="copy">Powered by Brightline Site Works © Copyright 2015</div>
    <nav class="footer-nav">
      <a href="#">Home</a><a href="#">Meet Our Staff</a><a href="#">Patient Testimonials</a><a href="#">Videos</a><a href="#">Work Place Wellness</a><a href="#">Contact</a>
    </nav>
    <a class="to-top" href="#"><svg viewBox="0 0 6 4"><path d="M.5 3.5L3 1l2.5 2.5"/></svg></a>
  </div>
</footer>

</body>
</html>
```